Dental clinic brochure design (Z fold)

We need a new brochure design made for our dental clinic - Corvellan Dental Surgery. One side is in English, the other is in Vietnamese - all text and translations provided in brochure sample with further instructions in word doc. We require a brochure design in a Z fold to convey a family friendly dental clinic, incorporating our logo colour into the theme and designers choice on complimentary colours. Additional high quality images are provided for use if required or free to use own images.

Colors
33b8a4
00a990
86cfc6

Requirements
Must have
• Easy to read font, flows from text to pictures and page to page
• At least 2 dental images

```html
<!DOCTYPE html>
<html lang="en">
<head>
<meta charset="utf-8">
<title>Corvellan Dental Surgery – Brochure Inside Spread</title>
<link href="https://fonts.googleapis.com/css2?family=Open+Sans:ital,wght@0,400;0,600;0,700;0,800;1,400&display=swap" rel="stylesheet">
<style>
  :root {
    --teal: #00a990;
    --teal-mid: #33b8a4;
    --teal-light: #86cfc6;
    --mint: #e2f2ee;
    --ink: #1f2d2b;
    --ink-soft: #5d6b69;
    --white: #ffffff;
    --page-bg: #f3f5f4;
  }
  * { box-sizing: border-box; margin: 0; padding: 0; }
  html, body {
    width: 1200px; height: 789px; overflow: hidden;
    background: var(--page-bg);
    font-family: "Open Sans", Arial, sans-serif;
    color: var(--ink);
  }
  .spread {
    position: relative; width: 1200px; height: 789px;
    display: grid; grid-template-columns: 400px 400px 400px;
    background: var(--white);
  }
  .panel { position: relative; height: 789px; }

  /* Left panel */
  .panel--scheme { background: var(--teal); color: var(--white); padding: 32px 36px 0; }
  .photo-kids {
    height: 210px; border-radius: 22px;
    background: linear-gradient(135deg, #f4e2c9 0%, #e7c37a 35%, #e46b6b 65%, #cfe08a 100%);
  }
  .scheme-kicker { margin-top: 22px; font-size: 21px; font-weight: 600; line-height: 1.15; }
  .scheme-title { font-size: 31px; font-weight: 800; line-height: 1.15; }
  .scheme-copy { margin-top: 10px; font-size: 12.5px; line-height: 1.5; opacity: .92; }
  .scheme-phone { margin-top: 6px; font-size: 26px; font-weight: 700; letter-spacing: .5px; line-height: 1.2; }

  /* Photo across left & middle */
  .photo-braces {
    position: absolute; left: 36px; top: 500px; width: 690px; height: 289px;
    border-radius: 22px 22px 0 0;
    background: linear-gradient(100deg, #e9e2d6 0%, #b9a9e6 28%, #f1d3bf 55%, #e8b8a3 75%, #6e4c36 100%);
  }

  /* Middle panel */
  .panel--promo { padding: 90px 40px 0 44px; }
  .promo-title { color: var(--teal); font-size: 38px; font-weight: 800; line-height: 1.05; }
  .promo-list { list-style: none; margin-top: 30px; }
  .promo-item { display: flex; gap: 12px; font-size: 15px; line-height: 1.45; margin-bottom: 22px; }
  .promo-item svg { flex: 0 0 18px; margin-top: 2px; }

  /* Right panel */
  .panel--providers { background: var(--mint); padding: 70px 34px 0; }
  .providers-title { color: var(--teal); font-size: 30px; font-weight: 800; font-style: italic; }
  .providers-card {
    margin-top: 24px; background: var(--white); border-radius: 22px;
    padding: 22px 22px 18px; height: 500px;
  }
  .provider { display: flex; gap: 12px; align-items: flex-start; margin-bottom: 16px; }
  .provider-avatar { width: 38px; height: 38px; border-radius: 4px; background: var(--teal-mid); flex: 0 0 38px; }
  .provider-name { font-size: 14px; font-weight: 700; }
  .provider-cred { font-size: 11px; color: var(--ink-soft); line-height: 1.35; }
  .map {
    margin-top: 6px; height: 150px; border-radius: 10px;
    background: linear-gradient(160deg, #f4f6f5 0%, #e6ebe9 100%);
  }
  .address {
    position: absolute; left: 34px; right: 34px; bottom: 22px;
    background: var(--teal); color: var(--white); border-radius: 22px;
    padding: 16px 22px; font-size: 12.5px; line-height: 1.55; text-align: center;
  }
  .address-title { font-size: 16px; font-weight: 700; margin-bottom: 4px; }
</style>
</head>
<body>
<main class="spread">
  <section class="panel panel--scheme">
    <div class="photo-kids" role="img" aria-label="Photo of smiling children holding toothbrushes"></div>
    <p class="scheme-kicker">Child Dental Scheme</p>
    <h2 class="scheme-title">Benefits Schedule</h2>
    <p class="scheme-copy">The child dental benefits program is available for eligible children aged 2 to 17 and will receive $1000 for dental treatments. To check if your children are eligible call us on</p>
    <p class="scheme-phone">(03) 9400 5172</p>
  </section>

  <section class="panel panel--promo">
    <h2 class="promo-title">Special<br>Promotions</h2>
    <ul class="promo-list">
      <li class="promo-item">
        <svg width="18" height="18" viewBox="0 0 18 18"><circle cx="9" cy="9" r="7.5" fill="none" stroke="var(--teal)" stroke-width="1.6"/><path d="M5.5 9.2l2.4 2.3 4.6-4.7" fill="none" stroke="var(--teal)" stroke-width="1.6"/></svg>
        <span>Gap free dental check-up, clean &amp; x-rays for all health insurances**</span>
      </li>
      <li class="promo-item">
        <svg width="18" height="18" viewBox="0 0 18 18"><circle cx="9" cy="9" r="7.5" fill="none" stroke="var(--teal)" stroke-width="1.6"/><path d="M5.5 9.2l2.4 2.3 4.6-4.7" fill="none" stroke="var(--teal)" stroke-width="1.6"/></svg>
        <span>At home whitening kit now $199 limited time only (normally $395)</span>
      </li>
      <li class="promo-item">
        <svg width="18" height="18" viewBox="0 0 18 18"><circle cx="9" cy="9" r="7.5" fill="none" stroke="var(--teal)" stroke-width="1.6"/><path d="M5.5 9.2l2.4 2.3 4.6-4.7" fill="none" stroke="var(--teal)" stroke-width="1.6"/></svg>
        <span>*Conditions apply —<br>Ask staff for more information</span>
      </li>
    </ul>
  </section>

  <section class="panel panel--providers">
    <h2 class="providers-title">Dental Providers</h2>
    <div class="providers-card">
      <div class="provider"><div class="provider-avatar"></div><div><p class="provider-name">Dr Lan Vo</p><p class="provider-cred">BDSc (Melb), ICCDE</p></div></div>
      <div class="provider"><div class="provider-avatar"></div><div><p class="provider-name">Dr Minh Tran</p><p class="provider-cred">BDSc (Melb), FICCDE FRACDS, MClinDent<br>Implants (Melb)</p></div></div>
      <div class="provider"><div class="provider-avatar"></div><div><p class="provider-name">Dr Thu Nguyen</p><p class="provider-cred">BHSc MDent (Latrobe)</p></div></div>
      <div class="provider"><div class="provider-avatar"></div><div><p class="provider-name">Dr Adam Ly</p><p class="provider-cred">BHSc MDent (Latrobe), FRACDS</p></div></div>
      <div class="provider"><div class="provider-avatar"></div><div><p class="provider-name">Dr Kate Ho</p><p class="provider-cred">BDS (Adl)</p></div></div>
      <div class="map" role="img" aria-label="Street map showing the clinic location"></div>
    </div>
    <div class="address">
      <p class="address-title">Address</p>
      <p>12 Corvellan Road Sunshine<br>Phone (03) 9400 5172<br>Email info@corvellandental.com</p>
    </div>
  </section>

  <div class="photo-braces" role="img" aria-label="Photo of a dentist examining a patient with braces"></div>
</main>
</body>
</html>
```